Quill Physical Therapy Website

I would need a clean modern website built to showcase my Physical therapy brand and services. I would need a simple but descriptive website that can ultimately connect my patients to my electronic medical portal so they may book an appointment..

```html
<!DOCTYPE html>
<html lang="en">
<head>
<meta charset="utf-8">
<title>Quill Physical Therapy</title>
<link href="https://fonts.googleapis.com/css2?family=Montserrat:wght@700;800;900&family=Roboto:ital,wght@0,400;0,500;0,700;1,400&display=swap" rel="stylesheet">
<style>
:root{
  --teal:#1b8c82;
  --teal-dark:#147068;
  --green:#7cc245;
  --blue:#4a5db3;
  --blue-dark:#3d4f9d;
  --ink:#1f1f1f;
  --muted:#666;
  --white:#fff;
}
*{box-sizing:border-box;margin:0;padding:0}
html,body{width:1200px;height:4708px;overflow:hidden}
body{font-family:'Roboto',sans-serif;color:var(--ink);background:var(--white);position:relative}
.abs{position:absolute}
.h-display{font-family:'Montserrat',sans-serif;font-weight:800;text-transform:uppercase;letter-spacing:.5px}
.teal{color:var(--teal)}.green{color:var(--green)}
.btn{position:absolute;display:flex;align-items:center;justify-content:center;gap:8px;background:var(--green);color:#fff;border-radius:30px;font-weight:700;font-size:14px;text-transform:uppercase;letter-spacing:.3px}
.btn .arr{width:14px;height:14px;border-radius:50%;background:#fff;display:inline-flex;align-items:center;justify-content:center}
.photo{position:absolute}
p.body{font-size:14px;line-height:28px;color:var(--muted)}

/* header */
.site-header{position:absolute;left:0;top:0;width:1200px;height:115px;background:#fff;z-index:3;box-shadow:0 2px 6px rgba(0,0,0,.06)}
.brand-badge{position:absolute;left:104px;top:-10px;width:196px;height:196px;border-radius:50%;background:#fff;z-index:4;display:flex;flex-direction:column;align-items:center;justify-content:center;box-shadow:0 3px 8px rgba(0,0,0,.08)}
.brand-badge .name{font-family:'Montserrat',sans-serif;font-weight:900;font-size:34px;color:var(--teal)}
.brand-badge .sub{font-family:'Montserrat',sans-serif;font-weight:700;font-size:8px;color:var(--teal);letter-spacing:.5px}
.call{position:absolute;left:636px;top:16px;display:flex;gap:12px;align-items:center}
.call .ico{width:34px;height:34px;border-radius:50%;background:var(--teal);display:flex;align-items:center;justify-content:center}
.call small{display:block;font-size:12px;color:#777}
.call strong{font-size:18px;font-weight:700}
.main-nav{position:absolute;left:490px;top:86px;display:flex;gap:30px;font-size:14px;font-weight:500}

/* hero */
.hero-photo{left:0;top:115px;width:1200px;height:630px;background:linear-gradient(100deg,#eef1ec 0%,#e3e7e2 45%,#c9cfc9 70%,#8d9693 100%)}
.hero h1{position:absolute;left:110px;top:288px;font-size:38px;line-height:44px}
.hero p{position:absolute;left:110px;top:395px;width:440px;font-size:16px;line-height:26px;color:#222}

/* about */
.about-art{left:120px;top:765px;width:380px;height:560px;background:radial-gradient(circle at 50% 35%,#e4f2ee 0,#f3f8f6 55%,#fff 75%)}
.about h2{position:absolute;left:600px;top:868px;font-size:36px;line-height:44px}

/* services */
.services-band{left:0;top:1408px;width:1200px;height:415px;background:linear-gradient(180deg,var(--teal) 0%,#178277 100%)}
.section-title{position:absolute;left:0;width:1200px;text-align:center;font-size:36px}
.service-card{position:absolute;width:310px;height:470px;background:#fff;border-radius:8px;box-shadow:0 6px 18px rgba(0,0,0,.16);text-align:center}
.service-card .img{position:absolute;left:8px;top:8px;width:294px;height:228px;border-radius:6px}
.icon-disc{position:absolute;left:122px;top:195px;width:66px;height:66px;border-radius:50%;background:var(--blue);border:4px solid #fff;display:flex;align-items:center;justify-content:center}
.service-card h3{position:absolute;left:0;top:282px;width:100%;font-size:16px;font-weight:700}
.service-card p{position:absolute;top:312px;left:20px;right:20px;font-size:13.5px;line-height:22px;color:var(--muted)}
.service-card .btn{left:80px;top:405px;width:150px;height:42px}

/* first visit */
.visit h2{position:absolute;left:110px;top:2180px;font-size:36px;line-height:42px}
.step{position:absolute;left:110px;width:430px}
.step .ic{position:absolute;left:0;top:2px;width:54px;height:54px;border-radius:50%;background:#eef1f8;display:flex;align-items:center;justify-content:center}
.step h4{margin-left:82px;font-size:15px;font-weight:700}
.step p{margin-left:82px;margin-top:14px;font-size:13.5px;line-height:22px;color:var(--muted)}
.visit-photo{left:600px;top:2133px;width:488px;height:512px;background:linear-gradient(160deg,#eef0ef 0%,#d6dbe0 55%,#8b94a0 100%)}

/* conditions */
.cond-tile{position:absolute;top:2892px;width:284px;height:288px}
.cond-tile span{position:absolute;left:0;right:0;bottom:18px;text-align:center;color:#fff;font-weight:700;font-size:18px}

/* testimonials */
.testi-band{left:0;top:3196px;width:1200px;height:376px;background:linear-gradient(90deg,#7cc245,#8fcb5e 50%,#7cc245)}
.avatar{position:absolute;width:160px;height:160px;border-radius:50%;border:4px solid rgba(255,255,255,.7)}
.quote-badge{position:absolute;width:42px;height:42px;border-radius:50%;background:var(--teal);color:#fff;font-family:'Montserrat',sans-serif;font-weight:900;font-size:26px;display:flex;align-items:center;justify-content:center}
.testimonial{position:absolute;width:300px;color:#fff}
.stars{color:#f3c623;font-size:15px;letter-spacing:2px}
.testimonial q{display:block;margin-top:8px;font-style:italic;font-size:14px;line-height:24px}
.testimonial b{display:block;margin-top:12px;font-size:13px}

/* blog */
.blog-card{position:absolute;top:3733px;width:306px;height:382px;background:#fff;border-radius:6px;box-shadow:0 4px 16px rgba(0,0,0,.12);text-align:center}
.blog-card .img{position:absolute;left:10px;top:10px;width:286px;height:205px}
.blog-card .date{position:absolute;left:0;top:234px;width:100%;display:flex;justify-content:center;align-items:center;gap:6px;font-size:13px;color:var(--blue)}
.blog-card h3{position:absolute;left:0;top:260px;width:100%;font-size:15.5px;font-weight:700}
.blog-card p{position:absolute;top:294px;left:24px;right:24px;font-size:13.5px;line-height:22px;color:var(--muted)}
.blog-card .more{position:absolute;left:0;top:346px;width:100%;display:flex;justify-content:center;align-items:center;gap:6px;font-size:13.5px;font-weight:700;color:var(--green);text-decoration:none}
.blog-card .more .arr{width:13px;height:13px;border-radius:50%;background:var(--green);display:inline-flex;align-items:center;justify-content:center}

/* footer */
.footer-band{left:0;top:4240px;width:1200px;height:400px;background:var(--blue)}
.footer-brand{left:110px;top:4470px;width:180px;text-align:center;color:#fff}
.footer-brand .name{font-family:'Montserrat',sans-serif;font-weight:900;font-size:40px}
.footer-brand .sub{font-family:'Montserrat',sans-serif;font-weight:700;font-size:9px;letter-spacing:.5px}
.footer-col{position:absolute;top:4362px;color:#fff}
.footer-col h5{font-family:'Montserrat',sans-serif;font-weight:800;font-size:15px;text-transform:uppercase;margin-bottom:22px}
.footer-col ul{list-style:none;font-size:11.5px;line-height:25px;padding-left:8px}
.contact-row{display:flex;gap:14px;font-size:11.5px;line-height:18px;margin-bottom:20px}
.subscribe p{font-size:11.5px;line-height:19px;width:240px}
.email-field{margin-top:18px;width:255px;height:36px;background:#fff;border-radius:20px;display:flex;align-items:center;padding-left:14px;font-size:11px;color:#888;position:relative}
.email-field .send{position:absolute;right:0;top:0;width:48px;height:36px;border-radius:0 20px 20px 0;background:var(--green);display:flex;align-items:center;justify-content:center}
.socials{display:flex;gap:10px;margin-top:22px}
.socials i{width:30px;height:30px;border-radius:50%;background:#fff;display:block}
.socials i.on{background:var(--green)}
.chat-bubble{left:1126px;top:4600px;width:44px;height:44px;border-radius:50%;background:var(--green)}
.bottom-bar{left:0;top:4640px;width:1200px;height:68px;background:var(--blue-dark);color:#fff;font-size:12.5px}
.bottom-bar .copy{position:absolute;left:110px;top:26px}
.bottom-bar .legal{position:absolute;right:110px;top:26px}
</style>
</head>
<body>

<header class="site-header">
  <div class="call">
    <span class="ico"><svg width="16" height="16" viewBox="0 0 24 24" fill="#fff"><path d="M6.6 10.8a15.1 15.1 0 0 0 6.6 6.6l2.2-2.2c.3-.3.7-.4 1-.2 1.1.4 2.3.6 3.6.6.6 0 1 .4 1 1V20c0 .6-.4 1-1 1A17 17 0 0 1 3 4c0-.6.4-1 1-1h3.5c.6 0 1 .4 1 1 0 1.3.2 2.5.6 3.6.1.3 0 .7-.2 1z"/></svg></span>
    <div><small>Call Us Today</small><strong>(123) 456 - 7890</strong></div>
  </div>
  <a class="btn" style="left:870px;top:18px;width:215px;height:44px;font-size:13px">Request Consultation</a>
  <nav class="main-nav"><span>Home</span><span>About Us</span><span>Services</span><span>Conditions</span><span>My Patients</span><span>Press</span><span>Contact</span></nav>
</header>
<div class="brand-badge"><span class="name">QUILL</span><span class="sub">PHYSICAL THERAPY &amp; WELLNESS</span></div>

<section class="hero">
  <div class="photo hero-photo" role="img" aria-label="Therapist guiding a patient through an overhead shoulder stretch in a bright clinic"></div>
  <h1 class="h-display"><span class="teal">Quill Physical</span><br><span class="green">Therapy</span></h1>
  <p>Lorem ipsum dolor sit amet, consectetur adipiscing elit, eiusmod incididunt magna aliqua.</p>
  <a class="btn" style="left:110px;top:478px;width:228px;height:46px">Request a Quote <span class="arr"><svg width="8" height="8" viewBox="0 0 10 10"><path d="M3 1l4 4-4 4" stroke="#7cc245" stroke-width="2" fill="none"/></svg></span></a>
  <svg class="abs" style="left:0;top:660px" width="1200" height="110" viewBox="0 0 1200 110" preserveAspectRatio="none">
    <path d="M0 60 C300 0 700 10 1200 40 L1200 110 L0 110Z" fill="var(--teal)"/>
    <path d="M0 80 C350 20 800 40 1200 55 L1200 110 L0 110Z" fill="#fff"/>
    <path d="M0 80 C350 20 800 40 1200 55" stroke="var(--green)" stroke-width="6" fill="none"/>
  </svg>
</section>

<section class="about">
  <div class="photo about-art" role="img" aria-label="Line illustration of a figure carrying a large round emblem"></div>
  <h2 class="h-display"><span class="teal">About Quill Physical</span><br><span class="green">Therapy</span></h2>
  <p class="body abs" style="left:600px;top:985px;width:470px">Lorem ipsum dolor sit amet, consectetur adipiscing elit, sed do eiusmod tempor incididunt ut labore et dolore magna aliqua. Ut enim ad minim veniam, quis nostrud exercitation ullamco laboris nisi ut aliquip ex ea commodo consequat.</p>
  <p class="body abs" style="left:600px;top:1112px;width:470px">Duis aute irure dolor in reprehenderit in voluptate velit esse cillum dolore eu fugiat nulla pariatur. Excepteur sint occaecat cupidatat non proident, sunt in culpa qui officia deserunt mollit anim id est laborum.</p>
  <a class="btn" style="left:600px;top:1233px;width:164px;height:42px">Read More <span class="arr"><svg width="8" height="8" viewBox="0 0 10 10"><path d="M3 1l4 4-4 4" stroke="#7cc245" stroke-width="2" fill="none"/></svg></span></a>
</section>

<section class="services">
  <div class="photo services-band"></div>
  <h2 class="section-title h-display" style="top:1455px;color:#fff">Our Services</h2>
  <article class="service-card" style="left:110px;top:1535px">
    <div class="img" style="background:linear-gradient(150deg,#e8e9ea,#b9c0c6 60%,#6e7b86)" role="img" aria-label="Therapist treating a patient's leg on a table"></div>
    <span class="icon-disc"><svg width="30" height="30" viewBox="0 0 24 24" fill="none" stroke="#fff" stroke-width="1.6"><circle cx="12" cy="5" r="2.5"/><path d="M12 8v7M7 11h10M9 21l3-6 3 6"/></svg></span>
    <h3>Services Title Here</h3>
    <p>Lorem ipsum dolor sit amet, consectetur adipiscing elit, sed do eiusmod tempor incididunt ut labore et</p>
    <a class="btn">Read More</a>
  </article>
  <article class="service-card" style="left:445px;top:1552px">
    <div class="img" style="background:linear-gradient(150deg,#eceae6,#c4c0b8 60%,#7a756c)" role="img" aria-label="Therapist stretching a patient's leg in a gym"></div>
    <span class="icon-disc"><svg width="30" height="30" viewBox="0 0 24 24" fill="none" stroke="#fff" stroke-width="1.6"><circle cx="12" cy="5" r="2.5"/><path d="M5 20h14M8 20v-6h8v6M12 8v6"/></svg></span>
    <h3>Services Title Here</h3>
    <p>Lorem ipsum dolor sit amet, consectetur adipiscing elit, sed do eiusmod tempor incididunt ut labore et</p>
    <a class="btn">Read More</a>
  </article>
  <article class="service-card" style="left:780px;top:1535px">
    <div class="img" style="background:linear-gradient(150deg,#e4e8ee,#a8b6c6 55%,#3f72b4)" role="img" aria-label="Patient exercising on a stability ball with a therapist"></div>
    <span class="icon-disc"><svg width="30" height="30" viewBox="0 0 24 24" fill="none" stroke="#fff" stroke-width="1.6"><circle cx="14" cy="5" r="2.5"/><path d="M4 18l6-5 4 3 6-6M4 21h16"/></svg></span>
    <h3>Services Title Here</h3>
    <p>Lorem ipsum dolor sit amet, consectetur adipiscing elit, sed do eiusmod tempor incididunt ut labore et</p>
    <a class="btn">Read More</a>
  </article>
</section>

<section class="visit">
  <h2 class="h-display"><span class="teal">Your First Quill</span><br><span class="green">Physical Visit</span></h2>
  <div class="step" style="top:2300px"><span class="ic"><svg width="28" height="28" viewBox="0 0 24 24" fill="none" stroke="var(--blue)" stroke-width="1.6"><circle cx="12" cy="6" r="2.5"/><path d="M6 20l6-11 6 11M8 14h8"/></svg></span><h4>Lorem ipsum dolor sit consectetur</h4><p>Lorem ipsum dolor sit amet, consectetur adipiscing elit, sed do eiusmod tempor incididunt</p></div>
  <div class="step" style="top:2405px"><span class="ic"><svg width="28" height="28" viewBox="0 0 24 24" fill="none" stroke="var(--blue)" stroke-width="1.6"><circle cx="12" cy="5" r="2.5"/><path d="M12 8v8M7 11h10M5 20h14"/></svg></span><h4>Lorem ipsum dolor sit consectetur</h4><p>Lorem ipsum dolor sit amet, consectetur adipiscing elit, sed do eiusmod tempor incididunt</p></div>
  <div class="step" style="top:2510px"><span class="ic"><svg width="28" height="28" viewBox="0 0 24 24" fill="none" stroke="var(--blue)" stroke-width="1.6"><circle cx="14" cy="5" r="2.5"/><path d="M4 19l6-6 4 3 6-6"/></svg></span><h4>Lorem ipsum dolor sit consectetur</h4><p>Lorem ipsum dolor sit amet, consectetur adipiscing elit, sed do eiusmod tempor incididunt</p></div>
  <div class="photo visit-photo" role="img" aria-label="Therapist assisting a seated patient with a resistance band exercise"></div>
</section>

<section class="conditions">
  <h2 class="section-title h-display" style="top:2748px"><span class="teal">Physical Therapy</span> <span class="green">Conditions</span></h2>
  <p class="abs" style="left:180px;top:2800px;width:840px;text-align:center;font-size:14px;line-height:25px;color:var(--muted)">Lorem ipsum dolor sit amet, consectetur adipiscing elit, sed do eiusmod tempor incididunt ut labore et dolore magna aliqua. Ut enim ad minim veniam, quis nostrud exercitation ullamco laboris nisi ea commodo consequat.</p>
  <div class="cond-tile" style="left:14px;background:linear-gradient(180deg,#b7aaa0,#7b6c63 70%,#3a3230)" role="img" aria-label="Back pain"><span>Back Pain</span></div>
  <div class="cond-tile" style="left:310px;background:linear-gradient(180deg,#d1cbc3,#8d8075 60%,#3c3733)" role="img" aria-label="Neck pain"><span>Neck Pain</span></div>
  <div class="cond-tile" style="left:606px;background:linear-gradient(180deg,#cfccc8,#8e8a86 60%,#3d3b39)" role="img" aria-label="Shoulder pain"><span>Shoulder Pain</span></div>
  <div class="cond-tile" style="left:902px;background:linear-gradient(180deg,#dcd9d6,#a39f9c 60%,#4a4745)" role="img" aria-label="Carpal tunnel"><span>Carpal Tunnel</span></div>
</section>

<section class="testimonials">
  <div class="photo testi-band"></div>
  <h2 class="section-title h-display" style="top:3258px;color:#fff">What Our Client Says</h2>
  <div class="avatar" style="left:115px;top:3340px;background:radial-gradient(circle,#e7c7b3,#a06a52)" role="img" aria-label="Client portrait"></div>
  <span class="quote-badge" style="left:172px;top:3462px">”</span>
  <div class="testimonial" style="left:297px;top:3352px"><div class="stars">★★★★★</div><q>Lorem ipsum dolor sit amet, consectetur adip is cing elit, sed do eiusmod tempor incididunt ut labore et dolore magna</q><b>John Doe</b></div>
  <div class="avatar" style="left:620px;top:3340px;background:radial-gradient(circle,#e6c8b2,#8a9ea8)" role="img" aria-label="Client portrait"></div>
  <span class="quote-badge" style="left:677px;top:3462px">”</span>
  <div class="testimonial" style="left:802px;top:3352px"><div class="stars">★★★★★</div><q>Lorem ipsum dolor sit amet, consectetur adip is cing elit, sed do eiusmod tempor incididunt ut labore et dolore magna</q><b>John Doe</b></div>
</section>

<section class="blog">
  <h2 class="section-title h-display teal" style="top:3660px">Latest Blog</h2>
  <article class="blog-card" style="left:108px"><div class="img" style="background:linear-gradient(150deg,#eceeef,#b8c1c9 60%,#5f6b78)" role="img" aria-label="Patient training with a resistance band"></div><span class="date"><svg width="12" height="12" viewBox="0 0 24 24" fill="none" stroke="var(--blue)" stroke-width="2.4"><rect x="3" y="5" width="18" height="16" rx="2"/><path d="M3 10h18M8 3v4M16 3v4"/></svg>February 2, 2021</span><h3>Lorem ipsum dolor sit amet,</h3><p>Sed ut perspiciatis unde omnis iste natus sit voluptatem accusantium</p><a class="more">READ MORE <span class="arr"><svg width="7" height="7" viewBox="0 0 10 10"><path d="M3 1l4 4-4 4" stroke="#fff" stroke-width="2" fill="none"/></svg></span></a></article>
  <article class="blog-card" style="left:443px"><div class="img" style="background:linear-gradient(150deg,#f1efec,#d3c8bc 60%,#d3825e)" role="img" aria-label="Therapist treating a patient's knee"></div><span class="date"><svg width="12" height="12" viewBox="0 0 24 24" fill="none" stroke="var(--blue)" stroke-width="2.4"><rect x="3" y="5" width="18" height="16" rx="2"/><path d="M3 10h18M8 3v4M16 3v4"/></svg>February 2, 2021</span><h3>Lorem ipsum dolor sit amet,</h3><p>Sed ut perspiciatis unde omnis iste natus sit voluptatem accusantium</p><a class="more">READ MORE <span class="arr"><svg width="7" height="7" viewBox="0 0 10 10"><path d="M3 1l4 4-4 4" stroke="#fff" stroke-width="2" fill="none"/></svg></span></a></article>
  <article class="blog-card" style="left:777px"><div class="img" style="background:linear-gradient(150deg,#e9ecef,#aab5c1 60%,#4d5b6c)" role="img" aria-label="Patient working out in a rehab gym"></div><span class="date"><svg width="12" height="12" viewBox="0 0 24 24" fill="none" stroke="var(--blue)" stroke-width="2.4"><rect x="3" y="5" width="18" height="16" rx="2"/><path d="M3 10h18M8 3v4M16 3v4"/></svg>February 2, 2021</span><h3>Lorem ipsum dolor sit amet,</h3><p>Sed ut perspiciatis unde omnis iste natus sit voluptatem accusantium</p><a class="more">READ MORE <span class="arr"><svg width="7" height="7" viewBox="0 0 10 10"><path d="M3 1l4 4-4 4" stroke="#fff" stroke-width="2" fill="none"/></svg></span></a></article>
</section>

<footer>
  <svg class="abs" style="left:0;top:4180px" width="1200" height="80" viewBox="0 0 1200 80" preserveAspectRatio="none">
    <path d="M0 70 C400 0 800 0 1200 20 L1200 80 L0 80Z" fill="var(--teal)"/>
    <path d="M0 80 C400 20 800 20 1200 35 L1200 80Z" fill="var(--blue)"/>
    <path d="M0 72 C400 12 800 14 1200 30" stroke="var(--green)" stroke-width="5" fill="none"/>
  </svg>
  <div class="photo footer-band"></div>
  <div class="abs footer-brand"><div class="name">QUILL</div><div class="sub">PHYSICAL THERAPY &amp; WELLNESS</div></div>
  <div class="footer-col" style="left:370px"><h5>Quick Links</h5><ul><li>Home</li><li>About Us</li><li>Services</li><li>Conditions</li><li>My Patients</li><li>Press</li><li>Contact</li></ul></div>
  <div class="footer-col" style="left:563px"><h5>Contact Us</h5>
    <div class="contact-row"><svg width="14" height="14" viewBox="0 0 24 24" fill="#fff"><path d="M6.6 10.8a15.1 15.1 0 0 0 6.6 6.6l2.2-2.2c.3-.3.7-.4 1-.2 1.1.4 2.3.6 3.6.6.6 0 1 .4 1 1V20c0 .6-.4 1-1 1A17 17 0 0 1 3 4c0-.6.4-1 1-1h3.5c.6 0 1 .4 1 1 0 1.3.2 2.5.6 3.6.1.3 0 .7-.2 1z"/></svg><span>555-0148</span></div>
    <div class="contact-row"><svg width="14" height="14" viewBox="0 0 24 24" fill="#fff"><path d="M3 5h18v14H3z"/><path d="M3 5l9 7 9-7" stroke="var(--blue)" stroke-width="2" fill="none"/></svg><span>info@quillpt.com</span></div>
    <div class="contact-row"><svg width="14" height="14" viewBox="0 0 24 24" fill="#fff"><path d="M12 2a7 7 0 0 0-7 7c0 5 7 13 7 13s7-8 7-13a7 7 0 0 0-7-7zm0 9.5A2.5 2.5 0 1 1 12 6.5a2.5 2.5 0 0 1 0 5z"/></svg><span>4120 Harbor Lane, Suite 12,<br>Maple Grove,</span></div>
    <div class="contact-row"><svg width="14" height="14" viewBox="0 0 24 24" fill="#fff"><rect x="3" y="5" width="18" height="14" rx="2"/></svg><span>555-0190</span></div>
  </div>
  <div class="footer-col subscribe" style="left:830px"><h5>Subscribe to Our Blog</h5>
    <p>Sign up today to get resources on how to attract and retain more customers!</p>
    <div class="email-field">Email Address<span class="send"><svg width="16" height="16" viewBox="0 0 24 24" fill="#fff"><path d="M2 21l21-9L2 3v7l15 2-15 2z"/></svg></span></div>
    <div class="socials"><i></i><i class="on"></i><i></i><i></i><i></i></div>
  </div>
  <div class="abs chat-bubble"><svg width="44" height="44" viewBox="0 0 44 44"><path d="M13 15h18v11H20l-5 4v-4h-2z" fill="#fff"/></svg></div>
  <div class="abs bottom-bar"><span class="copy">Copyright© 2021 <u>Quill Physical Therapy</u> | All Rights Reserved</span><span class="legal">Terms &amp; Condition &nbsp;|&nbsp; Site Map &nbsp;|&nbsp; Privacy Policy</span></div>
</footer>

</body>
</html>
```